Business Card - high end, modern health care

Hey designers!

We need a double sided business card for the boutique, cutting edge physical therapy rehabilitation centre in Sydney's Northern Beaches.

With the most qualified physios in the area The Harbourview Motion Clinic does what other physiotherapy practices do not, we take our time with our patients giving them longer appointments, better physios and therefor faster results!

We guarantee that the service people receive at THMC will be unparalleled.

Hence we need a business card to reflect our modern, boutique, high end service. The final design needs to reflect that we are in a class of our own yet with the feel of beachside retreat.

Below I have attached our logo in both blue on white and white on blue. The exact colour is;
and the font that we have used in our logo is Tex Gyre Aventador.

I like the idea of the blue as the main colour as it is more eye catching and our signage onto the main road will be in this blue and in the interest of consistency across marketing the blue needs to be a part of the design. However I would appreciate a few designs onto a wooden background as this is a visual theme within the fitout of the practice.

The design needs to be of standard size (91x55mm).

Target Market(s)

We target people who have an end outcome in mind and those who have had poor experiences with other providers and ensure that everyone gets the care that they deserve with a premium service that is tailored to the individuals circumstances. As a premium service, the target market is highly educated, business and tech savvy with the additional target market of elderly people who have self funded their retirement and see value in paying for the best ongoing rehabilitation to maintain independence.

Industry/Entity Type

Physical Therapy

Contact Information for Business Card

Name, designation( Titled Musculoskeletal Physiotherapist... there will also be those in the company that have multiple designations ie 5 or 6 words long), phone number, email, facebook, instagram, address

Font styles to use
Sans Serif

Colors

Designer to choose colors to be used in the design.

Requirements
Must have
• Front - The logo as large as possible, blue or wooden theme, and all of the important details.
• Back - A blank space/lines on which to write appointment times (no "Appointment, date, time" etc.)
Nice to have
• facebook url
• logos for facebook and instagram
• Mini logos for the phone and email?

```html
<!DOCTYPE html>
<html lang="en">
<head>
<meta charset="utf-8">
<title>The Harbourview Motion Clinic – Business Card</title>
<link rel="stylesheet" href="https://fonts.googleapis.com/css2?family=Montserrat:wght@400;500;700&display=swap">
<style>
  :root {
    --brand-blue: #1258a8;
    --ink: #2b2b2b;
    --rule: #6d6d6d;
    --paper: #ffffff;
    --backdrop: #e7e6e3;
  }
  * { box-sizing: border-box; margin: 0; padding: 0; }
  html, body { width: 1200px; height: 930px; overflow: hidden; }
  body {
    background: var(--backdrop);
    font-family: "Montserrat", sans-serif;
    color: var(--ink);
    display: flex;
    flex-direction: column;
    align-items: center;
    justify-content: center;
    gap: 60px;
  }
  .card {
    position: relative;
    width: 600px;
    height: 364px;
    background: var(--paper);
    border-radius: 16px;
    overflow: hidden;
    box-shadow: 0 6px 18px rgba(0,0,0,.18);
  }

  /* shared wordmark */
  .wordmark { display: flex; align-items: center; gap: 10px; }
  .wordmark__dot {
    width: 44px; height: 44px; border-radius: 50%;
    flex: none;
  }
  .wordmark__name {
    font-weight: 700;
    text-transform: uppercase;
    line-height: 1.1;
    letter-spacing: .02em;
  }

  /* back side */
  .card--back .back__band {
    position: absolute; left: 0; top: 0; right: 0; height: 150px;
    background: var(--brand-blue);
    display: flex; align-items: center; justify-content: center;
  }
  .card--back .wordmark__dot { background: var(--paper); }
  .card--back .wordmark__name { color: var(--paper); font-size: 20px; }
  .back__label {
    position: absolute; top: 172px; left: 0; right: 0;
    text-align: center;
    color: var(--brand-blue);
    font-size: 15px; font-weight: 500; letter-spacing: .03em;
  }
  .back__lines {
    position: absolute; left: 70px; right: 70px; top: 222px;
    display: flex; flex-direction: column; gap: 38px;
  }
  .back__lines span { display: block; height: 1px; background: var(--rule); }

  /* front side */
  .front__nameplate {
    position: absolute; left: 0; top: 48px;
    width: 268px; height: 72px;
    background: var(--brand-blue);
    color: var(--paper);
    padding: 12px 0 0 40px;
  }
  .front__name { font-size: 20px; font-weight: 700; text-transform: uppercase; letter-spacing: .01em; }
  .front__role { font-size: 12px; font-weight: 500; margin-top: 2px; }
  .front__logo {
    position: absolute; left: 244px; top: 42px;
  }
  .front__logo .wordmark__dot {
    width: 84px; height: 84px;
    background: var(--brand-blue);
    border: 6px solid var(--paper);
  }
  .front__logo .wordmark__name { color: var(--brand-blue); font-size: 23px; }
  .front__address {
    position: absolute; right: 36px; top: 196px;
    text-align: right; font-size: 13px; line-height: 1.45;
  }
  .front__contacts {
    position: absolute; left: 210px; bottom: 34px;
    list-style: none; font-size: 13px; line-height: 1.6;
  }
  .front__contacts li { display: flex; align-items: center; gap: 10px; }
  .front__contacts svg { width: 12px; height: 12px; fill: var(--brand-blue); flex: none; }
  .front__contacts .accent { color: var(--brand-blue); }
</style>
</head>
<body>

  <section class="card card--back" aria-label="Card back">
    <div class="back__band">
      <div class="wordmark">
        <span class="wordmark__dot"></span>
        <span class="wordmark__name">The Harbourview<br>Motion Clinic</span>
      </div>
    </div>
    <p class="back__label">Appointment</p>
    <div class="back__lines"><span></span><span></span><span></span></div>
  </section>

  <section class="card card--front" aria-label="Card front">
    <div class="front__nameplate">
      <p class="front__name">Daniel Hart</p>
      <p class="front__role">Director</p>
    </div>
    <div class="front__logo wordmark">
      <span class="wordmark__dot"></span>
      <span class="wordmark__name">The Harbourview<br>Motion Clinic</span>
    </div>
    <address class="front__address" style="font-style:normal">
      27 Shoreline Road, Unit 4,<br>Seaview, PO 20481
    </address>
    <ul class="front__contacts">
      <li>
        <svg viewBox="0 0 24 24" aria-hidden="true"><path d="M6.6 10.8a15.1 15.1 0 0 0 6.6 6.6l2.2-2.2c.3-.3.7-.4 1-.2 1.1.4 2.3.6 3.6.6.6 0 1 .4 1 1V20c0 .6-.4 1-1 1A17 17 0 0 1 3 4c0-.6.4-1 1-1h3.5c.6 0 1 .4 1 1 0 1.3.2 2.5.6 3.6.1.3 0 .7-.2 1z"/></svg>
        +330 2460-5173
      </li>
      <li>
        <svg viewBox="0 0 24 24" aria-hidden="true"><path d="M2 5h20v14H2zm2 2v.5l8 5 8-5V7zm0 2.8V17h16V9.8l-8 5z"/></svg>
        info@harbourviewmotion.com
      </li>
      <li>
        <svg viewBox="0 0 24 24" aria-hidden="true"><path d="M12 2a10 10 0 1 0 0 20 10 10 0 0 0 0-20zm0 2c.9 1.2 1.6 2.6 2 4h-4c.4-1.4 1.1-2.8 2-4zM4.3 14a8 8 0 0 1 0-4h3.4a16 16 0 0 0 0 4zm.8 2h3c.3 1.3.8 2.5 1.4 3.6A8 8 0 0 1 5.1 16zm3-8h-3a8 8 0 0 1 4.4-3.6C8.9 5.5 8.4 6.7 8.1 8zM12 20c-.9-1.2-1.6-2.6-2-4h4c-.4 1.4-1.1 2.8-2 4zm2.3-6H9.7a14 14 0 0 1 0-4h4.6a14 14 0 0 1 0 4zm.2 5.6c.6-1.1 1.1-2.3 1.4-3.6h3a8 8 0 0 1-4.4 3.6zM16.3 14a16 16 0 0 0 0-4h3.4a8 8 0 0 1 0 4zm-.4-6c-.3-1.3-.8-2.5-1.4-3.6A8 8 0 0 1 18.9 8z"/></svg>
        <span>www.<span class="accent">harbourviewmotion</span>.com</span>
      </li>
    </ul>
  </section>

</body>
</html>
```